Small legal and financial translation company needs Squarespace website, brochure and logo

Hello,
We are Lumarin Services (www.lumarinservices-example.com), a boutique legal and financial translation company. We offer our services mainly to Spanish customers. Our primary line of business is the translation of financial statements, but we translate a wide variety legal and financial texts.
The project we are offering comprises three parts: a redo of the current website, an informational brochure for potential customer and a logo design. These three parts should provide a consistent image. We would develop content soon.
We are looking for a website that would look like a typical law firm website, nothing too fancy. Right now, it is in English, Spanish and French, although the new site need only be in English and Spanish. There must be good toggling between the English and Spanish versions. There would be no need for tie-ins to social media and it would not contain a blog. Basically, a static site. We aren't interesting in driving traffic to the site or SEO, as we will contact nearly all potential customers beforehand. The website must be built in Squarespace to enable a smooth transition. The content would be similar to the current page, we'll be working on the exact content, but a rough draft is attached.
The brochure will be some three pages and would introduce the company to potential customers, using similar images as the website and the logo to be designed.
The only specifications for the logo is, as the website and brochure, it convey a sense of security and trust.
Feel free to ask with any questions as this is the first time we have used this platform.
Thank you!
Updates

I've added a more or less final version for the text in the brochure and updated the brief. Added Wednesday, June 10, 2015

Target Market(s)

Spanish law firms, auditors, accountants, banks, investment firms

Industry/Entity Type

Finance

Logo Text

Lumarin Services

Number of Pages Required

5+ page

Font styles to use
Serif

Requirements
Must have
• The website must be built in Squarespace and have a good option to toggle between English and Spanish versions.
• Brochure must be in both English and Spanish, I'm attaching a rough draft of the information that it will probably have. This should give an idea about what to include and the spacing. I will update it to include the final information.
Nice to have
• Would be nice to have some quality finance- and legal-related images
Should not have
• Vibrant colours

```html
<!DOCTYPE html>
<html lang="en">
<head>
<meta charset="utf-8">
<title>Lumarin Services – Brochure Pages 1 &amp; 2</title>
<link href="https://fonts.googleapis.com/css2?family=Cormorant+Garamond:wght@500;600&family=Crimson+Text:wght@400&family=Open+Sans:wght@400&display=swap" rel="stylesheet">
<style>
  :root {
    --backdrop: #d9d9d9;
    --backdrop-light: #f2f2f2;
    --paper: #ffffff;
    --ink: #3a3a3a;
    --ink-soft: #555555;
    --claret: #8a1424;
    --claret-dark: #5e0c18;
    --night: #0b0b0b;
    --night-light: #2a2a2a;
    --on-night: #e6e6e6;
  }
  * { box-sizing: border-box; margin: 0; padding: 0; }
  html, body { width: 1200px; height: 847px; overflow: hidden; }
  body {
    background: radial-gradient(ellipse at 50% 40%, var(--backdrop-light), var(--backdrop));
    font-family: "Crimson Text", Georgia, serif;
    color: var(--ink);
    position: relative;
  }
  .page-label {
    position: absolute; left: 30px; top: 34px;
    font-family: "Open Sans", Arial, sans-serif;
    font-size: 20px; color: #ffffff;
    text-shadow: 0 0 2px rgba(0,0,0,.15);
  }
  .spread {
    position: absolute; left: 110px; top: 110px;
    width: 980px; height: 630px;
    display: flex;
    box-shadow: 0 18px 40px rgba(0,0,0,.3);
  }
  .page { width: 490px; height: 100%; position: relative; overflow: hidden; }
  .page--intro { background: var(--paper); }
  .page--reasons {
    background: linear-gradient(100deg, var(--night) 0%, var(--night) 40%, var(--night-light) 70%, var(--night) 100%);
    color: var(--on-night);
  }
  .section-title {
    font-family: "Cormorant Garamond", Georgia, serif;
    font-variant: small-caps;
    font-weight: 600;
    letter-spacing: 1px;
  }
  .page--intro .section-title { color: var(--claret); font-size: 24px; }
  .about { position: absolute; left: 24px; top: 24px; right: 24px; display: flex; gap: 14px; }
  .about__visual { width: 190px; flex: none; }
  .about__visual .section-title { margin-bottom: 6px; }
  .about__photo {
    width: 190px; height: 150px;
    background: linear-gradient(135deg, #9a9a9a, #4a4a4a);
  }
  .about__text {
    font-size: 11.5px; line-height: 1.3; text-align: justify;
    color: var(--ink-soft); padding-top: 4px;
  }
  .experience { position: absolute; left: 24px; right: 24px; top: 232px; }
  .experience p {
    font-size: 11.5px; line-height: 1.3; text-align: justify;
    color: var(--ink-soft); margin-top: 6px;
  }
  .stats {
    position: absolute; left: 24px; right: 24px; top: 370px;
    display: flex; justify-content: space-between;
  }
  .stat { width: 130px; text-align: center; }
  .stat__ring {
    width: 120px; height: 96px; margin: 0 auto;
    border: 2px solid var(--claret); border-radius: 50%;
    display: flex; align-items: center; justify-content: center;
    font-family: "Cormorant Garamond", Georgia, serif;
    font-size: 36px; color: #222;
  }
  .stat__label { font-size: 11px; margin-top: 8px; color: var(--ink-soft); }
  .footer-band {
    position: absolute; left: 0; right: 0; bottom: 0; height: 62px;
    background: linear-gradient(180deg, var(--claret), var(--claret-dark));
    display: flex; align-items: center; padding-left: 24px;
    font-family: "Cormorant Garamond", Georgia, serif;
    font-size: 17px; font-weight: 600; letter-spacing: .5px; color: #ffffff;
  }
  .page--reasons .section-title { font-size: 24px; color: #ffffff; position: absolute; left: 30px; top: 24px; }
  .reasons { position: absolute; left: 30px; right: 28px; top: 70px; list-style: none; }
  .reason { display: flex; gap: 14px; margin-bottom: 22px; }
  .reason__icon {
    width: 30px; height: 30px; flex: none; margin-top: 10px;
    border: 1.5px solid var(--on-night); border-radius: 50%;
    display: flex; align-items: center; justify-content: center;
  }
  .reason__icon svg { width: 16px; height: 16px; fill: var(--on-night); stroke: var(--on-night); }
  .reason__title {
    font-family: "Cormorant Garamond", Georgia, serif;
    font-size: 16px; font-weight: 600; color: #ffffff;
  }
  .reason__text { font-size: 11px; line-height: 1.25; color: #c9c9c9; }
</style>
</head>
<body>
  <div class="page-label">Page 1 &amp; 2</div>

  <main class="spread">
    <section class="page page--intro">
      <div class="about">
        <div class="about__visual">
          <h2 class="section-title">Who Are We?</h2>
          <div class="about__photo" role="img" aria-label="Photograph of a team of business professionals in suits"></div>
        </div>
        <p class="about__text">We are a small, highly professional and qualified group of professionals with backgrounds in law, financial services and translation and interpretation that boasts experience in global consulting and auditing firms, law firms and companies from a cross section of industries. Sensitive to the workings of the financial world, we are detail-oriented experts striving to facilitate understanding among investors, companies and international organisations.</p>
      </div>

      <div class="experience">
        <h2 class="section-title">Experience You Can Trust On</h2>
        <p>Lorem ipsum dolor sit amet, consectetuer adipiscing elit, sed diam nonummy nibh euismod tincidunt ut laoreet dolore magna aliquam erat volutpat. Ut wisi enim ad minim veniam, quis nostrud exerci tation ullamcorper suscipit lobortis nisl ut aliquip ex ea commodo consequat. Duis autem vel eum iriure dolor in hendrerit in vulputate velit esse molestie consequat, vel illum dolore eu feugiat nulla facilisis at vero eros et accumsan et iusto odio.</p>
      </div>

      <div class="stats">
        <div class="stat"><div class="stat__ring">4589</div><p class="stat__label">Nos of Words Translated</p></div>
        <div class="stat"><div class="stat__ring">152</div><p class="stat__label">Nos of Documents Translated</p></div>
        <div class="stat"><div class="stat__ring">64</div><p class="stat__label">Nos of Satisfied Clients</p></div>
      </div>

      <footer class="footer-band">www.lumarinservices-example.com</footer>
    </section>

    <section class="page page--reasons">
      <h2 class="section-title">Why Choose Lumarin?</h2>
      <ul class="reasons">
        <li class="reason">
          <span class="reason__icon"><svg viewBox="0 0 16 16"><ellipse cx="8" cy="9" rx="6" ry="4.5" stroke="none"/><rect x="4" y="12" width="2" height="3" stroke="none"/><rect x="10" y="12" width="2" height="3" stroke="none"/></svg></span>
          <div><h3 class="reason__title">Save Money</h3><p class="reason__text">Lorem ipsum dolor sit amet, consectetuer adipiscing elit, sed diam nonummy nibh euismod tincidunt ut laoreet dolore magna aliquam erat volutpat. Ut wisi enim ad minim veniam, quis nostrud exerci tation ullamcorper suscipit lobortis nisl ut aliquip ex ea commodo consequat.</p></div>
        </li>
        <li class="reason">
          <span class="reason__icon"><svg viewBox="0 0 16 16"><polygon stroke="none" points="8,1 10,6 15,6 11,9.5 12.5,15 8,11.5 3.5,15 5,9.5 1,6 6,6"/></svg></span>
          <div><h3 class="reason__title">Quality Guaranteed</h3><p class="reason__text">Lorem ipsum dolor sit amet, consectetuer adipiscing elit, sed diam nonummy nibh euismod tincidunt ut laoreet dolore magna aliquam erat volutpat. Ut wisi enim ad minim veniam, quis nostrud exerci tation ullamcorper suscipit lobortis nisl ut aliquip ex ea commodo consequat.</p></div>
        </li>
        <li class="reason">
          <span class="reason__icon"><svg viewBox="0 0 16 16"><circle cx="8" cy="5" r="3" stroke="none"/><path d="M2 15 Q8 7 14 15 Z" stroke="none"/></svg></span>
          <div><h3 class="reason__title">Native Translators Only</h3><p class="reason__text">Lorem ipsum dolor sit amet, consectetuer adipiscing elit, sed diam nonummy nibh euismod tincidunt ut laoreet dolore magna aliquam erat volutpat. Ut wisi enim ad minim veniam, quis nostrud exerci tation ullamcorper suscipit lobortis nisl ut aliquip ex ea commodo consequat.</p></div>
        </li>
        <li class="reason">
          <span class="reason__icon"><svg viewBox="0 0 16 16"><circle cx="8" cy="8" r="6" fill="none" stroke-width="1.6"/><path d="M8 4 V8 H11" fill="none" stroke-width="1.6"/></svg></span>
          <div><h3 class="reason__title">Consistency Over Time</h3><p class="reason__text">Lorem ipsum dolor sit amet, consectetuer adipiscing elit, sed diam nonummy nibh euismod tincidunt ut laoreet dolore magna aliquam erat volutpat. Ut wisi enim ad minim veniam, quis nostrud exerci tation ullamcorper suscipit lobortis nisl ut aliquip ex ea commodo consequat.</p></div>
        </li>
        <li class="reason">
          <span class="reason__icon"><svg viewBox="0 0 16 16"><rect x="1.5" y="2.5" width="13" height="9" fill="none" stroke-width="1.6"/><rect x="5" y="13" width="6" height="1.6" stroke="none"/></svg></span>
          <div><h3 class="reason__title">Use of Technology Helps Cut Costs</h3><p class="reason__text">Lorem ipsum dolor sit amet, consectetuer adipiscing elit, sed diam nonummy nibh euismod tincidunt ut laoreet dolore magna aliquam erat volutpat. Ut wisi enim ad minim veniam, quis nostrud exerci tation ullamcorper suscipit lobortis nisl ut aliquip ex ea commodo consequat.</p></div>
        </li>
      </ul>
      <footer class="footer-band">www.lumarinservices-example.com</footer>
    </section>
  </main>
</body>
</html>
```